New Artwork Needed for a Wine Label

We need a wine label with the size, text, fonts being exactly like the one attached. However, we need the image of the stain glass bird and grapes being slightly different. We love this image of the bird and grapes in stained glass but can no longer use it, so we need to alter it a bit. The new name of the wine is "Sol Varra" (erase "Mirtesa"). The vintage is "2023" (Not 2018) All other text is the same.

To be clear: we wish to see the stain glass artwork showing the bird and grapes to be similar to what we currently have please.

Target Market(s)

US wine drinkers

Industry/Entity Type

wine sales

Font styles to use
Other font styles liked:
• It would be best to use the fonts that you see in attached label.

Requirements
Must have
• A new image of the bird and grapes in stained glass, similar to the one I am showing you, but different enough not to be exact.
Nice to have
• A new image of the bird and grapes in stained glass
Should not have
• A different image than a bird and grapes

```html
<!DOCTYPE html>
<html lang="en">
<head>
<meta charset="UTF-8">
<title>Sol Varra Moscato d'Asti Label</title>
<link rel="stylesheet" href="https://fonts.googleapis.com/css2?family=Sorts+Mill+Goudy&display=swap">
<style>
  :root {
    --canvas-bg: #f3f3f1;
    --label-paper: #ffffff;
    --ink: #2b2b2b;
    --ink-soft: #4a4a4a;
    --band-amber: #d9892a;
    --band-gold: #e7b54a;
    --band-violet: #8d7a98;
    --glass-pale: #e9efee;
    --glass-blue: #7fb4d6;
    --glass-orange: #e39a3c;
    --glass-grape: #8e3f6a;
    --glass-green: #b9c96a;
  }
  * { margin: 0; padding: 0; box-sizing: border-box; }
  html, body {
    width: 1000px;
    height: 1200px;
    overflow: hidden;
    background: var(--canvas-bg);
  }
  .label {
    position: absolute;
    left: 70px;
    top: 250px;
    width: 860px;
    height: 700px;
    background: var(--label-paper);
    box-shadow: 0 2px 10px rgba(0,0,0,0.08);
    font-family: "Sorts Mill Goudy", "Goudy Old Style", Georgia, serif;
    color: var(--ink);
  }
  .label__art-frame {
    position: absolute;
    left: 0;
    top: 0;
    width: 860px;
    height: 440px;
  }
  .label__art-frame svg { display: block; }
  .label__text {
    position: absolute;
    left: 0;
    top: 440px;
    width: 860px;
    height: 260px;
    text-align: center;
  }
  .label__wine-name {
    margin-top: 34px;
    font-size: 62px;
    font-weight: 400;
    letter-spacing: 1px;
    line-height: 1;
  }
  .label__designation {
    margin-top: 12px;
    font-size: 22px;
    color: var(--ink-soft);
    line-height: 1;
  }
  .label__vintage {
    margin-top: 22px;
    font-size: 44px;
    letter-spacing: 2px;
    line-height: 1;
  }
  .label__producer {
    margin-top: 18px;
    font-size: 56px;
    letter-spacing: 3px;
    line-height: 1;
    text-transform: uppercase;
  }
  .label__volume,
  .label__abv {
    position: absolute;
    top: 168px;
    font-size: 34px;
    line-height: 1;
  }
  .label__volume { left: 40px; }
  .label__abv { right: 40px; }
</style>
</head>
<body>
  <main class="label">
    <div class="label__art-frame">
      <svg width="860" height="440" viewBox="0 0 860 440">
        <defs>
          <linearGradient id="glass-artwork-tones" x1="0" y1="0" x2="0" y2="1">
            <stop offset="0" stop-color="var(--glass-pale)"/>
            <stop offset="0.35" stop-color="var(--glass-blue)"/>
            <stop offset="0.6" stop-color="var(--glass-orange)"/>
            <stop offset="0.82" stop-color="var(--glass-grape)"/>
            <stop offset="1" stop-color="var(--glass-green)"/>
          </linearGradient>
        </defs>
        <rect class="band band--top" x="0" y="0" width="860" height="14" fill="var(--band-amber)"/>
        <rect class="band band--top-accent" x="0" y="14" width="860" height="4" fill="var(--band-gold)"/>
        <rect class="stained-glass-art" x="0" y="18" width="860" height="398"
              fill="url(#glass-artwork-tones)" role="img"
              aria-label="Stained glass artwork of a blue and orange songbird perched among clusters of purple and green grapes"/>
        <rect class="band band--bottom" x="0" y="416" width="860" height="14" fill="var(--band-amber)"/>
        <rect class="band band--bottom-accent" x="0" y="430" width="860" height="10" fill="var(--band-violet)"/>
      </svg>
    </div>
    <section class="label__text">
      <h1 class="label__wine-name">MOSCATO D’ASTI</h1>
      <p class="label__designation">Denominazione di Origine Controllata e Garantita</p>
      <p class="label__vintage">2023</p>
      <p class="label__producer">Sol Varra</p>
      <span class="label__volume">750ml ℮</span>
      <span class="label__abv">5% vol</span>
    </section>
  </main>
</body>
</html>
```